Business Card - Tidal Lanes

Need Business Card design for company named Tidal Lanes. Software development focused mainly on Brindle Orvix & Zelt Apps. I've attached our logo with both a black and white background. Please add trademark symbol to logo when using.

```html
<!DOCTYPE html>
<html lang="en">
<head>
<meta charset="utf-8">
<title>Tidal Lanes – Business Card</title>
<link rel="stylesheet" href="https://fonts.googleapis.com/css2?family=Open+Sans:wght@400;600;700&display=swap">
<style>
  :root {
    --bg: #e9e9ee;
    --card-black: #000000;
    --orange: #fb9733;
    --red: #d51c16;
    --yellow: #f6b800;
    --white: #ffffff;
    --ink: #2a2a2a;
    --font: "Open Sans", sans-serif;
  }
  * { margin: 0; padding: 0; box-sizing: border-box; }
  html, body { width: 1200px; height: 987px; overflow: hidden; background: var(--bg); font-family: var(--font); }
  .stage { position: relative; width: 1200px; height: 987px; }

  .card { position: absolute; width: 620px; height: 354px; border-radius: 26px; overflow: hidden; background: var(--card-black); box-shadow: 0 10px 30px rgba(0,0,0,.18); }
  .card--back { left: 530px; top: 90px; }
  .card--front { left: 50px; top: 530px; }

  .brand { display: flex; align-items: center; gap: 10px; color: var(--white); font-weight: 700; letter-spacing: -0.5px; white-space: nowrap; }
  .brand__mark { width: 16px; height: 16px; background: var(--orange); }
  .brand__tm { font-size: 0.4em; align-self: flex-start; margin-top: 4px; }

  /* back */
  .card--back .brand { position: absolute; left: 0; right: 0; top: 120px; justify-content: center; font-size: 46px; }
  .card--back .brand__mark { width: 22px; height: 22px; }
  .web { position: absolute; left: 0; right: 0; top: 200px; text-align: center; color: var(--white); font-size: 20px; letter-spacing: 3px; }

  /* front */
  .front-art { position: absolute; inset: 0; width: 100%; height: 100%; }
  .card--front .brand { position: absolute; left: 40px; top: 108px; font-size: 30px; }
  .contacts { position: absolute; left: 40px; top: 172px; list-style: none; color: var(--white); font-size: 17px; }
  .contacts li { display: flex; align-items: center; gap: 10px; margin-bottom: 8px; }
  .contacts svg { width: 16px; height: 16px; }
  .holder { position: absolute; right: 28px; top: 140px; text-align: right; color: var(--ink); }
  .holder__name { font-size: 22px; font-weight: 700; line-height: 1.2; }
  .holder__title { font-size: 18px; font-weight: 400; line-height: 1.3; }
  .address { position: absolute; left: 320px; top: 282px; color: var(--white); font-size: 19px; line-height: 1.3; white-space: nowrap; }
</style>
</head>
<body>
<main class="stage">
  <section class="card card--back" aria-label="Card back">
    <div class="brand"><span class="brand__mark"></span>Tidal Lanes<span class="brand__tm">™</span></div>
    <p class="web">www.tidallanes.com</p>
  </section>

  <section class="card card--front" aria-label="Card front">
    <svg class="front-art" viewBox="0 0 620 354" aria-hidden="true">
      <path class="swoosh-orange" d="M0,0 H620 V354 H575 C520,170 330,60 0,34 Z" fill="var(--orange)"/>
      <path class="swoosh-red" d="M575,354 C520,170 330,60 0,34 L0,42 C320,70 495,178 548,354 Z" fill="var(--red)"/>
      <path class="swoosh-line" d="M40,22 C150,24 260,58 330,108" fill="none" stroke="var(--card-black)" stroke-width="3"/>
    </svg>
    <div class="brand"><span class="brand__mark"></span>Tidal Lanes<span class="brand__tm">™</span></div>
    <ul class="contacts">
      <li><svg viewBox="0 0 16 16"><rect x="4" y="1" width="8" height="14" rx="1.5" fill="var(--yellow)"/><rect x="5.5" y="3" width="5" height="6" fill="var(--card-black)"/></svg>555-214-0398</li>
      <li><svg viewBox="0 0 16 16"><path d="M3 4 L6 2 L8 5 L6.5 6.5 C7.5 8.5 8.5 9.5 10 10.5 L11.5 9 L14 11 L12 14 C7 13 3 9 3 4 Z" fill="var(--yellow)"/></svg>555-307-6182</li>
    </ul>
    <div class="holder">
      <p class="holder__name">Your Name</p>
      <p class="holder__title">Title</p>
    </div>
    <p class="address">4120 Harbor Row<br>Calden, FL 30912</p>
  </section>
</main>
</body>
</html>
```